Company Brochure and Presentation

Hello,

We are software development company and would like to design our company brochure (Both in high resolution Printable Format and PDF) and presentation (PPT).

The contents are ready for both assignment. Just need to align with creative design.

Please submit your portfolio so that we can short list and send you the contents.

Also, please include cost and time-frame.

Few more details for best quotation...

The company profile will have around 15 pages
The presentation (PPT) will also have 15 pages.

However, I am open for your suggestion to make it more professional designed, include more images and with less pages.

The files are attached herewith.

The rough images/ ideas for outsourcing models are provided in word file. Open for your ideas here.

Please review and let me know your best quote.

Also, please read below link before you quote so you can make a competitive bid.

http://www.pitchvale.example/quote-pitchvale.aspx?briefid=48203

Thanks & Best Regards,

Ramesh Kothari
Skype - ramesh.k.kothari
Updates

Hello All,

I hove uploaded few images like logo, banner etc. You can use those image or take as a reference. 

Also, please visit our website - www.zelvonix.example 

Thank you.

Target Market(s)

1. IT Department of the companies
2. Outsourcing IT companies
3. IT consultant

Industry/Entity Type

Software

```html
<!DOCTYPE html>
<html lang="en">
<head>
<meta charset="utf-8">
<title>Vision, Mission &amp; Objective — Zelvonix</title>
<link rel="stylesheet" href="https://fonts.googleapis.com/css2?family=Cormorant+Garamond:ital,wght@0,600;1,500&family=Lato:wght@300;400&display=swap">
<style>
  :root {
    --page-bg: #f1f1f2;
    --header-light: #fbfbfb;
    --header-grey: #dcdcdc;
    --brand-green: #8cc43c;
    --brand-green-dark: #74ad2a;
    --title-grey: #6b6b6b;
    --heading-green: #8cc43c;
    --body-grey: #b9b9b9;
    --logo-ink: #2a2a2a;
  }
  * { margin: 0; padding: 0; box-sizing: border-box; }
  html, body {
    width: 1200px; height: 797px; overflow: hidden;
    background: var(--page-bg);
  }
  .slide {
    position: relative;
    width: 1200px; height: 797px;
    background: var(--page-bg);
    font-family: "Lato", "Helvetica Neue", Arial, sans-serif;
  }
  .slide-header {
    position: absolute; left: 0; top: 0;
    width: 1200px; height: 64px;
  }
  .slide-header svg { position: absolute; inset: 0; }
  .slide-title {
    position: absolute; left: 43px; top: 16px;
    font-family: "Cormorant Garamond", Georgia, serif;
    font-style: italic; font-weight: 500;
    font-size: 27px; letter-spacing: 2px;
    color: var(--title-grey);
  }
  .brand {
    position: absolute; left: 1000px; top: 14px;
    display: flex; align-items: center; gap: 12px;
  }
  .brand-mark {
    width: 22px; height: 22px;
    border: 2px solid var(--logo-ink);
  }
  .brand-name {
    font-family: "Cormorant Garamond", Georgia, serif;
    font-weight: 600; font-size: 32px; line-height: 1;
    color: var(--logo-ink);
  }
  .illustration {
    position: absolute;
    border-radius: 8px;
  }
  .illustration--email {
    left: 285px; top: 125px; width: 195px; height: 262px;
    background: radial-gradient(ellipse at 50% 45%, #cfd9e2 0%, #e4e7ea 55%, var(--page-bg) 80%);
  }
  .illustration--team {
    left: 535px; top: 113px; width: 470px; height: 315px;
    background: radial-gradient(ellipse at 40% 40%, #c7d7e6 0%, #e2e5e8 55%, var(--page-bg) 82%);
  }
  .statement {
    position: absolute; left: 43px; width: 1097px;
  }
  .statement h2 {
    font-weight: 300; font-size: 27px; line-height: 1;
    color: var(--heading-green); letter-spacing: 0.5px;
    padding-bottom: 8px;
    border-bottom: 2px dotted var(--heading-green);
  }
  .statement p {
    margin-top: 10px;
    font-weight: 300; font-size: 19px; line-height: 1.2;
    color: var(--body-grey);
  }
  .statement--vision { top: 435px; }
  .statement--mission { top: 569px; }
  .statement--objective { top: 674px; }
</style>
</head>
<body>
<main class="slide">
  <header class="slide-header">
    <svg width="1200" height="64" viewBox="0 0 1200 64" aria-hidden="true">
      <defs>
        <linearGradient id="headerFade" x1="0" y1="0" x2="1" y2="0">
          <stop offset="0" stop-color="var(--header-light)"/>
          <stop offset="1" stop-color="var(--header-grey)"/>
        </linearGradient>
        <linearGradient id="headerShade" x1="0" y1="0" x2="0" y2="1">
          <stop offset="0" stop-color="#ffffff" stop-opacity="0"/>
          <stop offset="1" stop-color="#bdbdbd" stop-opacity="0.5"/>
        </linearGradient>
      </defs>
      <polygon points="0,0 487,0 547,64 0,64" fill="url(#headerFade)"/>
      <polygon points="0,0 487,0 547,64 0,64" fill="url(#headerShade)"/>
      <polygon points="487,0 1200,0 1200,64 547,64" fill="var(--brand-green)"/>
      <line x1="487" y1="0" x2="547" y2="64" stroke="var(--brand-green-dark)" stroke-width="2"/>
    </svg>
    <h1 class="slide-title">VISION, MISSION &amp; OBJECTIVE</h1>
    <div class="brand">
      <span class="brand-mark"></span>
      <span class="brand-name">Zelvonix</span>
    </div>
  </header>

  <div class="illustration illustration--email" role="img" aria-label="Illustration of a white figure holding a large blue email at-sign"></div>
  <div class="illustration illustration--team" role="img" aria-label="Illustration of white figures gathered around a blue globe and an open laptop"></div>

  <section class="statement statement--vision">
    <h2>VISION</h2>
    <p>To become a benchmark software solution provider in IT industry based on ethics, relationship and expertise.</p>
  </section>

  <section class="statement statement--mission">
    <h2>MISSION</h2>
    <p>To provide a qualitative solution through balancing triple constraints - Scope, Time and Cost.</p>
  </section>

  <section class="statement statement--objective">
    <h2>OBJECTIVE</h2>
    <p>To support our customer to overcome their business challenge and achieve the goal with right solution at right time.</p>
  </section>
</main>
</body>
</html>
```